Ward Compass Business Card Design*

We need a business card design for our company Ward Compass. Our company is specialized in providing online consulting services regarding medical institutions, hospitals and doctors. We work with patients worldwide looking to choose between healthcare providers. We have a website you may use as a reference, where we list doctors and clinics worldwide. So we target Medical providers as well as patients worldwide.
Target Market(s)
Medical Providers and patients around the world
Industry/Entity Type
Medical
Contact Information for Business Card
Salwa Kettani
CEO
+90 612 348 2175
info@wardcompass.example
www.wardcompass.example
14 Annakhil 7 H.R.B. Rabat, Morocco
Requirements
Must have
- Company logo/name on one full side, personal info and smaller logo and company name on the other side.
Nice to have
- Smart and elegant design

```html
<!DOCTYPE html>
<html lang="en">
<head>
<meta charset="utf-8">
<title>Ward Compass – Business Card</title>
<link href="https://fonts.googleapis.com/css2?family=Quicksand:wght@400;500;600&display=swap" rel="stylesheet">
<style>
  :root {
    --backdrop: #141414;
    --card: #2b2c2e;
    --ink-grey: #9a9b9d;
    --ink-soft: #7d7e80;
    --brand-blue: #2d58a8;
    --mark-grey: #8f9092;
  }
  * { margin: 0; padding: 0; box-sizing: border-box; }
  html, body {
    width: 1200px; height: 900px; overflow: hidden;
    background: var(--backdrop);
    font-family: "Quicksand", sans-serif;
  }
  .stage {
    position: relative; width: 1200px; height: 900px;
    display: flex; align-items: center; justify-content: center; gap: 60px;
  }
  .card {
    position: relative; width: 500px; height: 286px;
    background: var(--card);
    border-radius: 3px;
    overflow: hidden;
    box-shadow: 0 18px 40px rgba(0,0,0,.55);
  }

  /* Front: personal side */
  .card-front .brand {
    position: absolute; left: 28px; top: 30px;
    display: flex; align-items: center; gap: 10px;
  }
  .brand-dot {
    width: 22px; height: 22px; border-radius: 50%;
    background: var(--brand-blue);
  }
  .brand-name {
    font-size: 19px; font-weight: 500; letter-spacing: 1.5px;
    color: var(--brand-blue); text-transform: uppercase;
  }
  .address {
    position: absolute; left: 28px; top: 86px;
    font-size: 12.5px; line-height: 1.5; color: var(--ink-soft);
  }
  .contacts {
    position: absolute; left: 28px; top: 138px;
    list-style: none; font-size: 12.5px; color: var(--ink-soft);
  }
  .contacts li { display: flex; align-items: center; gap: 9px; height: 19px; }
  .contacts svg { width: 11px; height: 11px; fill: none; stroke: var(--brand-blue); stroke-width: 1.8; }
  .person {
    position: absolute; right: 24px; top: 112px; text-align: right;
  }
  .person-name { font-size: 21px; font-weight: 500; color: var(--ink-grey); }
  .person-name .first { color: var(--brand-blue); }
  .person-role { font-size: 11px; color: var(--ink-soft); margin-top: 1px; }

  /* Back: brand side */
  .card-back {
    display: flex; align-items: center; justify-content: center; gap: 16px;
  }
  .card-back .brand-dot { width: 40px; height: 40px; }
  .card-back .brand-name {
    font-size: 34px; letter-spacing: 3px; color: var(--mark-grey);
  }
</style>
</head>
<body>
<main class="stage">
  <section class="card card-front" aria-label="Business card front">
    <div class="brand">
      <span class="brand-dot"></span>
      <span class="brand-name">Ward Compass</span>
    </div>
    <p class="address">14 Annakhil<br>7 H.R.B. Rabat, Morocco</p>
    <ul class="contacts">
      <li>
        <svg viewBox="0 0 12 12"><path d="M2.5 1.2 L4.5 1.2 L5.3 3.6 L4 4.6 C4.7 6 6 7.3 7.4 8 L8.4 6.7 L10.8 7.5 L10.8 9.5 C10.8 10.3 10.2 10.8 9.5 10.8 C5.3 10.5 1.5 6.7 1.2 2.5 C1.2 1.8 1.7 1.2 2.5 1.2 Z"/></svg>
        +90 612 348 2175
      </li>
      <li>
        <svg viewBox="0 0 12 12"><rect x="1" y="2.5" width="10" height="7" rx="1"/><path d="M1.3 3 L6 6.6 L10.7 3"/></svg>
        info@wardcompass.example
      </li>
      <li>
        <svg viewBox="0 0 12 12"><circle cx="6" cy="6" r="4.8"/><path d="M1.2 6 H10.8 M6 1.2 C3.8 3.5 3.8 8.5 6 10.8 M6 1.2 C8.2 3.5 8.2 8.5 6 10.8"/></svg>
        www.wardcompass.example
      </li>
    </ul>
    <div class="person">
      <p class="person-name"><span class="first">Salwa</span> Kettani</p>
      <p class="person-role">CEO</p>
    </div>
  </section>

  <section class="card card-back" aria-label="Business card back">
    <span class="brand-dot"></span>
    <span class="brand-name">Ward Compass</span>
  </section>
</main>
</body>
</html>
```